MRT Property - Business Cards

Looking for a business card & general letterhead, signage etc design for our new logo.

Colours:
000a20
0056a2
00b5ef
0088ce
68cef2

Fonts:
Poppins
Karla

Please keep look and feel of new brand - example in the zip package I sent.

```html
<!DOCTYPE html>
<html lang="en">
<head>
<meta charset="utf-8">
<title>MRT Property – Business Cards</title>
<link href="https://fonts.googleapis.com/css2?family=Poppins:wght@400;500;600;700&family=Karla:wght@400;500&display=swap" rel="stylesheet">
<style>
  :root{
    --ink:#000a20;
    --brand-deep:#0056a2;
    --brand-bright:#00b5ef;
    --brand-mid:#0088ce;
    --brand-light:#68cef2;
    --stage:#2a2a2c;
    --paper:#ffffff;
    --mist:#eef1f6;
    --rule:#8a8f99;
  }
  *{box-sizing:border-box;margin:0;padding:0}
  html,body{width:1200px;height:866px;overflow:hidden;background:var(--stage)}
  .sheet{position:relative;width:1200px;height:866px}
  .card{position:absolute;top:278px;width:540px;height:309px;overflow:hidden;box-shadow:0 10px 24px rgba(0,0,0,.45)}
  .card--back{left:30px;background:linear-gradient(125deg,#0a4f96 0%,var(--brand-mid) 38%,#3fb2ea 70%,var(--brand-bright) 100%)}
  .card--front{left:630px;background:var(--paper)}
  .card__art{position:absolute;inset:0;width:100%;height:100%}
  .wordmark{position:absolute;font-family:"Poppins",sans-serif;font-weight:600;letter-spacing:.06em;white-space:nowrap;display:flex;align-items:center;gap:12px}
  .card--back .wordmark{left:0;right:0;top:134px;justify-content:center;color:var(--paper);font-size:40px;line-height:1}
  .wordmark__dot{width:26px;height:26px;border-radius:50%;background:currentColor;flex:none}
  .card--front .wordmark{right:34px;top:114px;color:var(--brand-deep);font-size:30px;line-height:1}
  .contact{position:absolute;left:30px;top:36px;font-family:"Poppins",sans-serif;color:var(--ink)}
  .contact__name{font-weight:700;font-size:16px;letter-spacing:.06em;color:var(--brand-deep);text-transform:uppercase;line-height:1.3}
  .contact__role{font-size:12px;margin-top:2px}
  .contact__rule{position:absolute;left:30px;top:82px;width:250px;height:1px;background:var(--rule)}
  .contact__lines{position:absolute;left:30px;top:92px;font-family:"Karla",sans-serif;font-size:13px;color:var(--ink);line-height:1.55}
  .contact__line{display:flex;align-items:center;gap:7px}
  .contact__line svg{width:12px;height:12px;flex:none}
  .address{position:absolute;right:34px;top:206px;text-align:right;font-family:"Karla",sans-serif;font-size:13px;line-height:1.35;color:var(--ink)}
  .address__rule{position:absolute;right:34px;top:198px;width:260px;height:1px;background:var(--rule)}
  .website{position:absolute;right:34px;bottom:9px;font-family:"Karla",sans-serif;font-size:13px;letter-spacing:.02em;color:var(--paper)}
</style>
</head>
<body>
<main class="sheet">

  <section class="card card--back" aria-label="Business card, back">
    <svg class="card__art" viewBox="0 0 540 309" preserveAspectRatio="none" aria-hidden="true">
      <path d="M0 309 C40 190 150 90 330 30 C200 40 80 70 0 110 Z" fill="#083f7a" opacity=".3"/>
      <path d="M60 309 C110 190 230 110 420 70 C300 130 200 210 170 309 Z" fill="#ffffff" opacity=".08"/>
      <path d="M250 0 C360 40 470 60 540 50 L540 0 Z" fill="#ffffff" opacity=".07"/>
    </svg>
    <div class="wordmark"><span class="wordmark__dot"></span>MRT PROPERTY</div>
  </section>

  <section class="card card--front" aria-label="Business card, front">
    <svg class="card__art" viewBox="0 0 540 309" preserveAspectRatio="none" aria-hidden="true">
      <path d="M0 40 C120 -10 300 -5 460 60 C320 30 160 60 60 309 L0 309 Z" fill="var(--mist)" opacity=".7"/>
      <path d="M0 262 L150 282 C175 286 185 290 200 290 L0 290 Z" fill="var(--brand-light)"/>
      <path d="M0 270 L160 292 C180 294 190 276 215 274 L540 274 L540 309 L0 309 Z" fill="var(--brand-deep)"/>
      <path d="M0 268 L160 290 L160 292 L0 270 Z" fill="#ffffff"/>
    </svg>

    <div class="contact">
      <p class="contact__name">Daniel Reeves</p>
      <p class="contact__role">Managing Director</p>
    </div>
    <div class="contact__rule"></div>
    <div class="contact__lines">
      <p class="contact__line">
        <svg viewBox="0 0 12 12" aria-hidden="true"><path d="M3 1 L4.6 3.4 L3.6 4.6 C4.2 6 5.4 7.3 7 8 L8.2 7 L10.8 8.6 L9.8 10.8 C5.6 10.6 1.4 6.4 1 2.2 Z" fill="var(--brand-deep)"/></svg>
        044-507 318 624
      </p>
      <p class="contact__line">
        <svg viewBox="0 0 12 12" aria-hidden="true"><rect x="0.5" y="2" width="11" height="8" fill="var(--brand-deep)"/><path d="M0.5 2 L6 6.5 L11.5 2" stroke="#fff" stroke-width="1" fill="none"/></svg>
        hello@mrtproperty.net
      </p>
    </div>

    <div class="wordmark">MRT PROPERTY</div>

    <div class="address__rule"></div>
    <p class="address">27 Crescent Road, Unit 5<br>60218, Westhaven</p>
    <p class="website">www.mrtproperty.net</p>
  </section>

</main>
</body>
</html>
```